We need a laundry sheet packingbox desgin

-look at our website lindavel.nl to be in line with our house style/collor
We are a perfume seller and would like to offer also wasshingsheets with NO SMELL, so the customers can buy this incombination with our washingperfumes.
-the wassingheets will be neutrale(NO SMELL)
-it will be for the Dutch market
The next points should be on the desgin of the package
-our brand name: LINDAVEL
-product name: WASSTRIPS
-(contains) Bevat: 30 wasstrips
-30 wasstrips = 60 wasbeurten
Please take some inspiration of others sellers & regarding eco friendly symbols etc.:
voltirra.com & plomkens.nl
Backside information will be provided afther we found the right desgin
Please look at attachement pdf open box.
Here you can find the pdf design where you need to customize:
https://fz.qx/t-kR8bNwL2sY

```html
<!DOCTYPE html>
<html lang="nl">
<head>
<meta charset="utf-8">
<title>LINDAVEL Wasstrips – verpakking uitslag</title>
<link href="https://fonts.googleapis.com/css2?family=Marcellus&family=Domine:wght@400;700&family=Courier+Prime:wght@700&family=Oswald:wght@400;500&family=Lora:ital,wght@0,400;0,600;1,400&display=swap" rel="stylesheet">
<style>
  :root{
    --ink:#141414;
    --pattern-dark:#151515;
    --pattern-mid:#2b2b2b;
    --gold:#c9a32c;
    --gold-light:#e4c65c;
    --paper:#ffffff;
    --cut:#d41f26;
    --stage:#f2f2f0;
  }
  *{box-sizing:border-box;margin:0;padding:0}
  html,body{width:951px;height:1200px;overflow:hidden;background:var(--stage)}
  .dieline-sheet{position:absolute;left:0;top:271px;width:1604px;height:1110px;transform:scale(0.5929);transform-origin:0 0;overflow:hidden;font-family:"Domine",serif;color:var(--ink)}
  .layer{position:absolute;left:0;top:0;width:1604px;height:1110px}
  .abs{position:absolute}
  .brand{font-family:"Marcellus",serif;letter-spacing:1px;display:flex;align-items:center;gap:14px;white-space:nowrap}
  .brand-dot{width:30px;height:30px;border-radius:50%;flex:none}
  .brand--white{color:var(--paper);font-size:27px}
  .brand--white .brand-dot{background:var(--paper)}
  .brand--gold{color:var(--gold);font-size:34px}
  .brand--gold .brand-dot{background:var(--gold)}
  .product-tag{color:var(--paper);font-weight:700;font-size:24px;letter-spacing:1px}
  .intro-copy{left:195px;top:249px;width:560px;font-family:"Courier Prime",monospace;font-weight:700;font-size:14px;line-height:19.6px;letter-spacing:.2px;color:var(--paper);white-space:nowrap}
  .howto-title{left:165px;top:456px;width:572px;text-align:center;font-family:"Marcellus",serif;font-size:17.5px;font-weight:400}
  .step-text{width:112px;font-family:"Lora",serif;font-size:7.4px;line-height:9px;top:614px}
  .step-text b{display:block;color:var(--gold);font-weight:600;font-size:7px;letter-spacing:.3px;margin-top:8px}
  .step-text b:first-child{margin-top:0}
  .step-text i{display:block;font-style:italic}
  .warning{left:193px;top:735px;width:514px;height:58px;border:1.6px solid var(--ink);border-radius:8px;font-family:"Lora",serif;font-size:9.4px;line-height:10.4px}
  .warning svg{position:absolute;left:8px;top:10px}
  .warning .col{position:absolute;top:5px;width:230px}
  .maker{left:365px;top:810px;font-size:15.5px;line-height:20px;font-family:"Lora",serif;font-style:normal}
  .maker strong{font-family:"Domine",serif;font-size:15px}
  .maker .web{font-family:"Courier Prime",monospace;font-weight:700;font-size:16px;display:flex;align-items:center;gap:10px;letter-spacing:1px}
  .vert{writing-mode:vertical-rl}
  .vert-up{writing-mode:vertical-rl;transform:rotate(180deg)}
  .side-brand{left:737px;top:200px;width:128px;display:flex;flex-direction:column;align-items:center;gap:10px;color:var(--gold);font-family:"Marcellus",serif;font-size:30px;letter-spacing:1px}
  .side-brand .brand-dot{background:var(--gold)}
  .big-name{font-weight:700;font-size:46px;letter-spacing:2px;font-family:"Domine",serif}
  .side-name{left:737px;top:555px;width:128px;display:flex;justify-content:center}
  .hero-name{left:950px;top:282px;width:400px;text-align:center;color:var(--gold);font-weight:700;font-size:52px;letter-spacing:1px}
  .claim{text-align:center;color:var(--paper);top:368px}
  .claim .lead{font-size:27px;letter-spacing:.5px;padding-bottom:2px;border-bottom:1.5px solid var(--gold);display:inline-block}
  .claim .sub{font-size:23px;line-height:30px}
  .claim .small{font-size:13.5px;letter-spacing:.8px}
  .free-of{width:50px;border:2px solid;border-radius:7px;display:flex;flex-direction:column;align-items:center;overflow:hidden}
  .free-of .tab{background:var(--gold);color:var(--ink);font-family:"Oswald",sans-serif;font-weight:500;font-size:12px;line-height:13px;padding:6px 5px;text-align:center;width:100%;display:flex;justify-content:center}
  .free-of .list{font-family:"Oswald",sans-serif;font-size:11.3px;line-height:12.5px;padding:6px 4px;letter-spacing:.4px}
  .free-of--dark{left:887px;top:312px;height:233px;border-color:var(--paper);color:var(--paper);background:var(--ink)}
  .free-of--light{left:887px;top:568px;height:232px;border-color:var(--ink);color:var(--ink);background:var(--paper)}
  .count{width:120px;text-align:center;top:700px}
  .count .word{font-size:15.5px;line-height:17px}
  .count .num{font-size:38px;font-weight:700;line-height:38px}
  .count .pill{display:inline-block;border:1.3px solid var(--gold);border-radius:8px;font-size:15.5px;line-height:16px;padding:1px 8px;font-weight:700}
  .benefits{left:1185px;font-family:"Oswald",sans-serif;font-size:14.5px;line-height:16px;letter-spacing:.6px;list-style:none}
  .benefits li{display:flex;align-items:center;gap:5px}
  .panel-count{display:flex;align-items:center;gap:6px;font-family:"Domine",serif}
  .panel-count .num{font-size:28px;font-weight:700}
  .panel-count .pill{border:1.2px solid var(--gold);border-radius:7px;font-size:14px;font-weight:700;padding:6px 1px}
  .peel{font-family:"Oswald",sans-serif;font-size:15px;letter-spacing:.5px}
</style>
</head>
<body>
<main class="dieline-sheet" aria-label="LINDAVEL Wasstrips doos, uitslag">

  <!-- artwork base -->
  <svg class="layer" viewBox="0 0 1604 1110">
    <defs>
      <radialGradient id="patternTone" cx="50%" cy="35%" r="75%">
        <stop offset="0" stop-color="var(--pattern-mid)"/>
        <stop offset="1" stop-color="var(--pattern-dark)"/>
      </radialGradient>
      <linearGradient id="sheetTone" x1="0" y1="0" x2="1" y2="1">
        <stop offset="0" stop-color="#ffffff"/>
        <stop offset="0.6" stop-color="#f1f1f1"/>
        <stop offset="1" stop-color="#d6d6d6"/>
      </linearGradient>
      <linearGradient id="iconTone" x1="0" y1="0" x2="0" y2="1">
        <stop offset="0" stop-color="#fbf3d8"/>
        <stop offset="1" stop-color="#ecd48a"/>
      </linearGradient>
      <radialGradient id="sealTone" cx="40%" cy="35%" r="70%">
        <stop offset="0" stop-color="var(--gold-light)"/>
        <stop offset="1" stop-color="#a9841c"/>
      </radialGradient>
    </defs>
    <rect class="pattern-field" width="1604" height="1110" fill="url(#patternTone)" role="img" aria-label="Donker sierpatroon van bloemmotieven"/>
    <path class="paper-wave" d="M0 555 C150 480 300 430 420 440 C560 452 700 510 850 545 C1000 575 1200 540 1400 545 C1500 548 1560 545 1604 542 L1604 1110 L0 1110 Z" fill="var(--paper)"/>
  </svg>

  <!-- cut and fold lines -->
  <svg class="layer dieline" viewBox="0 0 1604 1110" fill="none" stroke="var(--cut)" stroke-width="1.6">
    <path d="M165 163 L737 163 L737 945 L165 945 Z"/>
    <path d="M165 55 L50 55 Q44 55 43 62 L39 163 L39 945 L44 1050 Q45 1058 52 1058 L160 1058 L165 945"/>
    <path d="M167 163 L172 60 Q174 48 187 48 L715 48 Q727 48 729 60 L737 163"/>
    <rect x="195" y="75" width="510" height="70"/>
    <path d="M243 75 V145 M291 75 V145 M339 75 V145 M387 75 V145 M435 75 V145 M483 75 V145 M531 75 V145 M579 75 V145 M627 75 V145 M675 75 V145" stroke-dasharray="5 5"/>
    <path d="M737 163 L742 62 Q744 52 754 52 L850 52 Q860 52 861 62 L865 163"/>
    <path d="M737 945 L865 945 M865 163 L1442 163 L1442 945 L865 945 L865 163"/>
    <path d="M865 163 L877 50 Q878 38 890 38 L1420 38 Q1432 38 1432 50 L1442 163"/>
    <path d="M1442 165 L1555 165 Q1564 165 1564 178 L1564 350 Q1545 352 1540 365 L1540 745 Q1545 760 1564 760 L1564 935 Q1563 945 1550 945 L1442 945"/>
    <path d="M172 945 L177 1055 Q178 1065 190 1065 L715 1065 Q727 1065 728 1055 L737 945"/>
    <rect x="195" y="975" width="510" height="60"/>
    <path d="M243 975 V1035 M291 975 V1035 M339 975 V1035 M387 975 V1035 M435 975 V1035 M483 975 V1035 M531 975 V1035 M579 975 V1035 M627 975 V1035 M675 975 V1035" stroke-dasharray="5 5"/>
    <path d="M742 945 L747 1055 Q748 1065 760 1065 L850 1065 Q860 1065 861 1055 L865 945"/>
    <path d="M877 945 L877 1065 Q878 1075 890 1075 L1420 1075 Q1432 1075 1432 1065 L1432 945"/>
    <path d="M950 325 L950 262 L1480 262 Q1510 265 1520 300 L1540 360 M1540 760 L1520 820 Q1505 848 1470 850 L1000 850 L950 850 L950 750" stroke-dasharray="7 5"/>
    <path d="M1000 255 V270 M1000 843 V857"/>
  </svg>

  <!-- BACK PANEL -->
  <div class="abs brand brand--white" style="left:236px;top:196px"><span class="brand-dot"></span>LINDAVEL</div>
  <div class="abs product-tag" style="left:490px;top:197px">•WASSTRIPS•</div>
  <p class="abs intro-copy">Lorem ipsum dolor sit amet, consectetuer adipiscing elit,<br>sed diam nonummy nibh euismod tincidunt ut laoreet<br>dolore magna aliquam erat volutpat. Ut wisi enim ad<br>minim veniam, quis nostrud exerci tation ullamcorper<br>suscipit lobortis nisl ut aliquip ex ea commodo consequat.<br>Duis autem vel eum iriure dolor in hendrerit in vulputate<br>velit esse molestie consequat, vel illum dolore eu feugiat<br>nulla facilisis at vero eros et accumsan et iusto odio</p>

  <h2 class="abs howto-title">GEBRUIK / HOW TO USE</h2>
  <svg class="abs" style="left:195px;top:478px" width="560" height="135" viewBox="195 478 560 135">
    <g fill="var(--paper)" stroke="var(--ink)" stroke-width="1.5">
      <rect x="207" y="492" width="114" height="113" rx="6"/>
      <rect x="331" y="492" width="114" height="113" rx="6"/>
      <rect x="455" y="492" width="114" height="113" rx="6"/>
      <rect x="579" y="492" width="114" height="113" rx="6"/>
    </g>
    <g fill="url(#iconTone)">
      <rect x="217" y="508" width="94" height="88" rx="4" role="img" aria-label="Illustratie: wasvel in de wasmachine leggen"/>
      <rect x="341" y="508" width="94" height="88" rx="4" role="img" aria-label="Illustratie: wasgoed in de wasmachine doen"/>
      <rect x="465" y="508" width="94" height="88" rx="4" role="img" aria-label="Illustratie: wasmachine draait"/>
      <rect x="589" y="508" width="94" height="88" rx="4" role="img" aria-label="Illustratie: schone gevouwen kleding"/>
    </g>
    <g fill="var(--paper)" stroke="var(--ink)" stroke-width="1.3">
      <circle cx="264" cy="492" r="10"/><circle cx="388" cy="492" r="10"/><circle cx="512" cy="492" r="10"/><circle cx="636" cy="492" r="10"/>
    </g>
    <g font-family="Lora, serif" font-size="13" text-anchor="middle" fill="var(--ink)">
      <text x="264" y="497">1</text><text x="388" y="497">2</text><text x="512" y="497">3</text><text x="636" y="497">4</text>
    </g>
  </svg>
  <div class="abs step-text" style="left:211px"><b>VOEG EEN WASVEL TOE</b><i>Plaats één wasvel in de wasmachine (gebruik twee voor grote of sterk bevuilde ladingen).</i><b>ADD SHEET</b><i>Place one sheet in the washing machine (use two for large or heavily soiled loads).</i></div>
  <div class="abs step-text" style="left:335px"><b>VOEG WASGOED TOE</b><i>Voeg je kleding toe zoals gewoonlijk.</i><b>LOAD LAUNDRY</b><i>Add your clothes as usual.</i></div>
  <div class="abs step-text" style="left:459px"><b>START DE WASBEURT</b><i>Selecteer je wasprogramma. Geen vloeibaar wasmiddel of poeder nodig – het wasvel doet al het werk!</i><b>START WASH</b><i>Select your wash cycle. No need for liquid detergent or powder – just let the sheet do the work!</i></div>
  <div class="abs step-text" style="left:583px"><b>GENIET VAN FRISSE WAS</b><i>Ervaar elke keer zachte, schone en fris ruikende kleding.</i><b>ENJOY FRESH LAUNDRY</b><i>Experience soft, clean, and fresh-smelling clothes every time.</i></div>

  <div class="abs warning">
    <svg width="36" height="34" viewBox="0 0 36 34"><path d="M18 2 L34 31 L2 31 Z" fill="none" stroke="var(--ink)" stroke-width="2.4" stroke-linejoin="round"/><path d="M18 12 V22" stroke="var(--ink)" stroke-width="3"/><circle cx="18" cy="26.5" r="1.8" fill="var(--ink)"/></svg>
    <p class="col" style="left:54px">Buiten bereik van kinderen en huisdieren houden. Contact met de ogen vermijden. Bij contact, grondig spoelen met water. Niet inslikken. Bij inslikken, medisch advies inwinnen. Bewaar op een koele, droge plaats, uit direct zonlicht.</p>
    <p class="col" style="left:290px">Keep out of reach of children and pets. Avoid contact with eyes. If contact occurs, rinse thoroughly with water. Do not ingest. If swallowed, seek medical advice. Store in a cool, dry place away from direct sunlight.</p>
  </div>

  <address class="abs maker">
    <strong>LINDAVEL</strong><br>
    Lindelaan 27<br>
    Lindelaan 27, 1017 KV Amsterdam,<br>
    Netherlands
    <span class="web"><svg width="12" height="12" viewBox="0 0 12 12" fill="none" stroke="var(--ink)" stroke-width="1.2"><circle cx="6" cy="6" r="5"/><path d="M1 6 H11 M6 1 C3 4 3 8 6 11 C9 8 9 4 6 1"/></svg>www.lindavel.nl</span>
  </address>

  <!-- SIDE PANEL -->
  <div class="abs side-brand"><span class="brand-dot"></span><span class="vert">LINDAVEL</span></div>
  <div class="abs side-name"><span class="vert big-name">•WASSTRIPS•</span></div>

  <!-- FRONT TOP FLAP -->
  <div class="abs brand brand--gold" style="left:1010px;top:85px;transform:rotate(180deg)"><span class="brand-dot"></span>LINDAVEL</div>

  <!-- FRONT PANEL -->
  <div class="abs brand brand--gold" style="left:1015px;top:198px"><span class="brand-dot"></span>LINDAVEL</div>
  <h1 class="abs hero-name">•WASSTRIPS•</h1>
  <div class="abs claim" style="left:950px;width:185px"><span class="lead">GEEN GEUR</span><div class="sub">Waslakens</div><div class="small">Lost op in de was</div></div>
  <div class="abs claim" style="left:1160px;width:190px"><span class="lead">NO SMELL</span><div class="sub">Washing Sheets</div><div class="small">Dissolves in the wash</div></div>

  <svg class="abs" style="left:1000px;top:460px" width="420" height="200" viewBox="0 0 420 200">
    <rect x="10" y="8" width="285" height="175" rx="14" fill="url(#sheetTone)" role="img" aria-label="Afbeelding van een wit wasvel met omgekrulde hoek"/>
    <circle cx="350" cy="118" r="57" fill="url(#sealTone)" role="img" aria-label="Kwaliteitszegel"/>
  </svg>

  <div class="abs free-of free-of--dark">
    <span class="tab vert">GEMAAKT<br>ZONDER</span>
    <span class="list vert">•DYES •FORMALDEHYDE<br>•PHTHALATES •1,4-DIOXANE<br>NEVER TESTED ON ANIMALS</span>
  </div>
  <div class="abs free-of free-of--light">
    <span class="tab vert">MADE<br>WITHOUT</span>
    <span class="list vert">•DYES •FORMALDEHYDE<br>•PHTHALATES •1,4-DIOXANE<br>NEVER TESTED ON ANIMALS</span>
  </div>

  <div class="abs count" style="left:955px"><div class="word">bevat</div><div class="num">30</div><span class="pill">· vellen ·</span><div class="num">60</div><div class="word">wasbeurten</div></div>
  <div class="abs count" style="left:1062px"><div class="word">contains</div><div class="num">30</div><span class="pill">· sheets ·</span><div class="num">60</div><div class="word">washes</div></div>

  <ul class="abs benefits" style="top:684px">
    <li><svg width="10" height="9" viewBox="0 0 10 9"><path d="M1 5 L4 8 L9 1" fill="none" stroke="var(--gold)" stroke-width="1.5"/></svg>HYPOALLERGENIC</li>
    <li><svg width="10" height="9" viewBox="0 0 10 9"><path d="M1 5 L4 8 L9 1" fill="none" stroke="var(--gold)" stroke-width="1.5"/></svg>PLANT POWERED</li>
    <li><svg width="10" height="9" viewBox="0 0 10 9"><path d="M1 5 L4 8 L9 1" fill="none" stroke="var(--gold)" stroke-width="1.5"/></svg>PLASTIC-VRIJE VERPAKKING</li>
    <li><svg width="10" height="9" viewBox="0 0 10 9"><path d="M1 5 L4 8 L9 1" fill="none" stroke="var(--gold)" stroke-width="1.5"/></svg>VLEKKENBESTRIJDENDE ENZYMEN</li>
  </ul>
  <ul class="abs benefits" style="top:759px">
    <li><svg width="10" height="9" viewBox="0 0 10 9"><path d="M1 5 L4 8 L9 1" fill="none" stroke="var(--gold)" stroke-width="1.5"/></svg>HYPOALLERGENIC</li>
    <li><svg width="10" height="9" viewBox="0 0 10 9"><path d="M1 5 L4 8 L9 1" fill="none" stroke="var(--gold)" stroke-width="1.5"/></svg>PLANT POWERED</li>
    <li><svg width="10" height="9" viewBox="0 0 10 9"><path d="M1 5 L4 8 L9 1" fill="none" stroke="var(--gold)" stroke-width="1.5"/></svg>PLASTIC-FREE PACKAGING</li>
    <li><svg width="10" height="9" viewBox="0 0 10 9"><path d="M1 5 L4 8 L9 1" fill="none" stroke="var(--gold)" stroke-width="1.5"/></svg>STAIN-FIGHTING ENZYMES</li>
  </ul>

  <!-- RIGHT SIDE PANEL -->
  <div class="abs panel-count vert" style="left:1490px;top:190px;color:var(--paper)"><span class="num">30</span><span class="pill">· vellen ·</span></div>
  <div class="abs vert-up big-name" style="left:1452px;top:370px;color:var(--gold);font-size:50px">•WASSTRIPS•</div>
  <div class="abs vert-up peel" style="left:1537px;top:365px;color:var(--paper)">OPTILLEN EN TERUGSCHILLEN</div>
  <div class="abs vert-up peel" style="left:1537px;top:585px;color:var(--ink)">LIFT UP AND PEEL BACK</div>
  <div class="abs panel-count vert" style="left:1490px;top:862px;color:var(--ink)"><span class="num">30</span><span class="pill">· sheets ·</span></div>

</main>
</body>
</html>
```